Brivolt Technologies business card design

We need a business card designed with our new logo. it would be great if the card could communicate it is a technology based company.

Target Market(s)

system integrators

Industry/Entity Type

technology, IOT

Contact Information for Business Card

Name, designation, Address, telephone number, email address

Requirements
Must have
• logo and company name
Nice to have
• something to do with technology

```html
<!DOCTYPE html>
<html lang="en">
<head>
<meta charset="utf-8">
<title>Brivolt Technologies – Business Card</title>
<link rel="stylesheet" href="https://fonts.googleapis.com/css2?family=Oswald:wght@500&family=Inter:wght@400&display=swap">
<style>
  :root {
    --backdrop: #141414;
    --card: #1d1d1d;
    --card-edge: #262626;
    --silver: #cfcfcf;
    --silver-soft: #a9a9a9;
  }
  * { margin: 0; padding: 0; box-sizing: border-box; }
  html, body { width: 1200px; height: 900px; overflow: hidden; }
  body {
    background: var(--backdrop);
    display: flex;
    flex-direction: column;
    align-items: center;
    justify-content: center;
    gap: 36px;
  }
  .card {
    width: 700px;
    height: 400px;
    background: var(--card);
    border: 1px solid var(--card-edge);
    position: relative;
  }
  .card-front {
    display: flex;
    align-items: center;
    justify-content: center;
  }
  .brand {
    display: flex;
    align-items: center;
    gap: 18px;
    color: var(--silver);
    font-family: "Oswald", sans-serif;
    font-weight: 500;
    font-size: 44px;
    letter-spacing: 3px;
    text-transform: uppercase;
  }
  .brand-mark {
    width: 44px;
    height: 44px;
    background: var(--silver);
  }
  .card-back {
    display: flex;
    align-items: center;
    justify-content: center;
  }
  .person {
    flex: none;
    text-align: right;
    padding-right: 24px;
  }
  .person-name {
    font-family: "Oswald", sans-serif;
    font-weight: 500;
    font-size: 32px;
    letter-spacing: 2px;
    color: var(--silver);
    text-transform: uppercase;
    line-height: 1.1;
    white-space: nowrap;
  }
  .person-role {
    font-family: "Inter", sans-serif;
    font-size: 17px;
    color: var(--silver-soft);
    letter-spacing: 1px;
    margin-top: 6px;
  }
  .divider {
    flex: none;
    width: 1px;
    height: 150px;
    background: var(--silver-soft);
  }
  .contact {
    flex: none;
    padding-left: 24px;
    font-family: "Inter", sans-serif;
    font-size: 18px;
    color: var(--silver);
    line-height: 1.45;
    list-style: none;
    white-space: nowrap;
  }
  .contact li { display: flex; align-items: center; gap: 8px; }
  .contact svg { width: 15px; height: 15px; flex: none; }
</style>
</head>
<body>
  <section class="card card-front">
    <div class="brand">
      <span class="brand-mark"></span>
      <span class="brand-name">Brivolt Technologies</span>
    </div>
  </section>

  <section class="card card-back">
    <div class="person">
      <p class="person-name">Daniel Hartmann</p>
      <p class="person-role">DIRECTOR</p>
    </div>
    <span class="divider"></span>
    <ul class="contact">
      <li>1417 Cedar Hollow Road</li>
      <li>Lakeview, MI 48850</li>
      <li>
        <svg viewBox="0 0 16 16" fill="none" stroke="#cfcfcf" stroke-width="1.6" stroke-linecap="round"><path d="M4 2 L6 5 L5 6.5 Q6.5 9.5 9.5 11 L11 10 L14 12 L12.5 14 Q6 13 2 5 Z"/></svg>
        (555) 418-3072
      </li>
      <li>
        <svg viewBox="0 0 16 16" fill="none" stroke="#cfcfcf" stroke-width="1.4"><rect x="2" y="4" width="12" height="9"/><path d="M2 4 L8 9 L14 4"/></svg>
        hello@brivolttech.com
      </li>
      <li>
        <svg viewBox="0 0 16 16" fill="none" stroke="#cfcfcf" stroke-width="1.3"><circle cx="8" cy="8" r="6"/><ellipse cx="8" cy="8" rx="2.6" ry="6"/><path d="M2 8 H14"/></svg>
        brivolttechnologies.com
      </li>
    </ul>
  </section>
</body>
</html>
```